A4 Folder presentation Design Project

A4 Folder presentation Design.

A4 presentation folder, need to have company logo on it and aligned with company colors

Uploaded my business cards as a reference

Target Market(s)

Business owners

Industry/Entity Type

Electrical

Font styles to use
Sans Serif

Requirements
Must have
• Company logo

Company colors
Orange R:240 G:86 B:47
Blue R:4 G:116 B:187
Dark Grey

```html
<!DOCTYPE html>
<html lang="en">
<head>
<meta charset="UTF-8">
<title>Crestline Electrical – Presentation Folder</title>
<link rel="stylesheet" href="https://fonts.googleapis.com/css2?family=Open+Sans:wght@400;600;700&display=swap">
<style>
  :root{
    --orange:#f0562f;
    --orange-soft:#f6845f;
    --blue:#0474bb;
    --blue-light:#3aa3de;
    --blue-deep:#1d5fc2;
    --white:#ffffff;
    --grey-dark:#3a3f47;
    --sky:#dfe9f0;
    --city:#8a9bb0;
    --water:#cfe3ec;
    --page:#eceef1;
  }
  *{box-sizing:border-box;margin:0;padding:0}
  html,body{width:1200px;height:848px;overflow:hidden}
  body{background:var(--page);font-family:"Open Sans",Arial,sans-serif;position:relative}
  .cover{position:absolute;top:127px;width:420px;height:594px;overflow:hidden;background:var(--white);box-shadow:0 6px 18px rgba(0,0,0,.18)}
  .cover--front{left:150px}
  .cover--back{left:630px}
  .cover__photo{position:absolute;inset:0;
    background:linear-gradient(180deg,var(--sky) 0%,var(--city) 45%,#7d8ea3 62%,var(--water) 72%,#e9f2f6 100%)}
  .cover__shapes{position:absolute;inset:0;width:100%;height:100%}
  .cover__title{position:absolute;left:34px;top:70px;color:var(--white);line-height:1.08}
  .cover__title span{display:block}
  .cover__title .light{font-weight:400;font-size:34px}
  .cover__title .bold{font-weight:700;font-size:38px}
  .brand{position:absolute;display:flex;align-items:center;gap:8px;color:var(--blue);font-weight:700;font-size:15px;letter-spacing:.5px;text-transform:uppercase}
  .brand__dot{width:22px;height:22px;border-radius:50%;background:var(--orange);flex:none}
  .cover--front .brand{right:30px;bottom:150px}
  .cover--back .brand{left:40px;bottom:120px}
  .contact{position:absolute;right:28px;bottom:200px;list-style:none;font-size:11px;color:var(--grey-dark)}
  .contact li{display:flex;align-items:center;gap:7px;margin-bottom:5px}
  .contact svg{width:11px;height:11px;fill:var(--orange);flex:none}
</style>
</head>
<body>

<section class="cover cover--front">
  <div class="cover__photo" role="img" aria-label="City skyline across the water"></div>
  <svg class="cover__shapes" viewBox="0 0 420 594" preserveAspectRatio="none">
    <defs>
      <linearGradient id="frontBlue" x1="0" y1="1" x2="1" y2="0">
        <stop offset="0" stop-color="var(--blue-light)" stop-opacity=".85"/>
        <stop offset="1" stop-color="var(--blue)" stop-opacity=".9"/>
      </linearGradient>
      <linearGradient id="frontOrange" x1="0" y1="0" x2="1" y2="0">
        <stop offset="0" stop-color="var(--orange-soft)"/>
        <stop offset=".35" stop-color="var(--orange)"/>
      </linearGradient>
    </defs>
    <polygon points="0,235 160,250 420,110 420,440 220,440 0,430" fill="url(#frontBlue)"/>
    <polygon points="0,214 160,228 420,85 420,110 160,252 0,238" fill="var(--white)"/>
    <polygon points="0,0 420,0 420,85 160,228 0,214" fill="url(#frontOrange)"/>
  </svg>
  <h1 class="cover__title">
    <span class="light">Business</span>
    <span class="bold">Presentation</span>
    <span class="bold">Folder</span>
  </h1>
  <div class="brand"><span class="brand__dot"></span>Crestline Electrical</div>
</section>

<section class="cover cover--back">
  <div class="cover__photo" role="img" aria-label="City skyline across the water"></div>
  <svg class="cover__shapes" viewBox="0 0 420 594" preserveAspectRatio="none">
    <defs>
      <linearGradient id="backBlue" x1="0" y1="0" x2="1" y2="0">
        <stop offset="0" stop-color="var(--blue-light)" stop-opacity=".9"/>
        <stop offset=".5" stop-color="var(--blue)" stop-opacity=".95"/>
        <stop offset="1" stop-color="var(--blue-deep)" stop-opacity=".85"/>
      </linearGradient>
      <linearGradient id="backOrange" x1="0" y1="0" x2="1" y2="0">
        <stop offset="0" stop-color="var(--orange-soft)"/>
        <stop offset=".4" stop-color="var(--orange)"/>
      </linearGradient>
    </defs>
    <polygon points="0,72 420,50 420,230 0,230" fill="url(#backBlue)"/>
    <polygon points="0,58 420,36 420,50 0,72" fill="var(--white)"/>
    <polygon points="80,0 420,0 420,36 0,58" fill="url(#backOrange)"/>
  </svg>
  <ul class="contact">
    <li><svg viewBox="0 0 24 24"><path d="M6.6 10.8a15.1 15.1 0 0 0 6.6 6.6l2.2-2.2a1 1 0 0 1 1-.25 11.4 11.4 0 0 0 3.6.57 1 1 0 0 1 1 1V20a1 1 0 0 1-1 1A17 17 0 0 1 3 4a1 1 0 0 1 1-1h3.5a1 1 0 0 1 1 1c0 1.25.2 2.45.57 3.6a1 1 0 0 1-.25 1z"/></svg>0400 318 725</li>
    <li><svg viewBox="0 0 24 24"><path d="M2 5h20v14H2zm2 2v.5l8 5 8-5V7z"/></svg>hello@crestline-power.com.au</li>
    <li><svg viewBox="0 0 24 24"><circle cx="12" cy="12" r="10"/></svg>crestline-power.com.au</li>
    <li><svg viewBox="0 0 24 24"><path d="M12 3 2 12h3v8h5v-5h4v5h5v-8h3z"/></svg>Your Street Address Here, 64789</li>
  </ul>
  <div class="brand"><span class="brand__dot"></span>Crestline Electrical</div>
</section>

</body>
</html>
```